Website visual upgrade

I am seeking expressions of interest for the updating the visuals of my website www.kelvastaffing.net
I am basically seeking a simple,bold and visually strong graphic makeover.using existing or shortly to be modified text.

```html
<!DOCTYPE html>
<html lang="en">
<head>
<meta charset="utf-8">
<title>Kelva Staffing</title>
<link rel="stylesheet" href="https://fonts.googleapis.com/css2?family=PT+Sans:wght@400;700&family=PT+Sans+Narrow:wght@700&display=swap">
<style>
  :root {
    --brand-red: #c8102e;
    --ink: #333333;
    --ink-soft: #555555;
    --ink-dark: #1f1f1f;
    --rule: #cfcfcf;
    --page: #ffffff;
    --hero-light: #f2f4f5;
    --hero-mid: #d9dde0;
    --social-blue: #3b5a9a;
    --social-sky: #2aa3d9;
    --social-orange: #f26b1d;
    --social-red: #d9302a;
  }
  * { box-sizing: border-box; margin: 0; padding: 0; }
  html, body { width: 1027px; height: 1200px; overflow: hidden; background: var(--page); }
  body { font-family: "PT Sans", Arial, sans-serif; color: var(--ink); position: relative; }

  .site-header { position: absolute; top: 0; left: 0; width: 1027px; height: 106px; }
  .brand { position: absolute; left: 75px; top: 30px; display: flex; align-items: center; gap: 12px; }
  .brand-dot { width: 26px; height: 26px; border-radius: 50%; background: var(--ink-dark); }
  .brand-name { font-size: 36px; font-weight: 700; color: var(--brand-red); letter-spacing: .5px; }
  .account-links { position: absolute; right: 73px; top: 17px; font-size: 14px; font-weight: 700; color: var(--ink-dark); letter-spacing: .3px; }
  .search { position: absolute; right: 73px; top: 55px; width: 194px; height: 30px; border: 1px solid #c9c9c9; border-radius: 4px; font-size: 11px; font-style: italic; color: #999; padding: 8px 6px; }
  .search svg { position: absolute; right: 9px; top: 8px; }

  .main-nav { position: absolute; top: 106px; left: 0; width: 1027px; height: 42px; background: var(--brand-red); }
  .main-nav ul { list-style: none; display: flex; gap: 18.5px; position: absolute; left: 84px; top: 12px; }
  .main-nav li { color: #fff; font-size: 14.5px; text-transform: uppercase; }

  .hero { position: absolute; top: 148px; left: 0; width: 1027px; height: 358px; }
  .hero-photo { position: absolute; inset: 0; background: linear-gradient(90deg, var(--hero-light) 0%, var(--hero-mid) 38%, #e9eef1 55%, #b9bec3 75%, #e4e8ea 100%); }
  .hero-copy { position: absolute; left: 76px; top: 115px; }
  .hero-title { font-family: "PT Sans Narrow", "Arial Narrow", sans-serif; font-size: 29px; color: var(--brand-red); letter-spacing: .3px; }
  .hero-subtitle { font-size: 20px; color: #444; margin-top: 2px; letter-spacing: .3px; }
  .hero-text { font-size: 14px; color: #444; line-height: 21px; margin-top: 6px; width: 360px; }
  .hero-button { display: inline-block; margin-top: 17px; width: 135px; height: 36px; background: var(--brand-red); color: #fff; font-size: 17px; text-align: center; line-height: 36px; }
  .hero-dots { position: absolute; left: 78px; top: 330px; display: flex; gap: 3px; }
  .hero-dots span { width: 7px; height: 7px; border-radius: 50%; background: #333; }
  .hero-dots span.is-active { background: transparent; border: 1px solid #333; }

  .features { position: absolute; top: 544px; left: 0; width: 1027px; }
  .feature { position: absolute; width: 260px; }
  .feature svg { position: absolute; left: 0; top: 0; }
  .feature-title { position: absolute; top: 0; font-size: 22px; color: var(--brand-red); white-space: nowrap; }
  .feature-sub { position: absolute; top: 32px; font-size: 13.5px; color: var(--ink-dark); white-space: nowrap; }
  .feature-text { position: absolute; top: 65px; left: 1px; width: 258px; font-size: 11.3px; line-height: 18.5px; color: var(--ink); }

  .section-title { font-size: 17px; color: var(--brand-red); position: absolute; }
  .welcome-photo { position: absolute; left: 75px; top: 739px; width: 188px; height: 182px; border-radius: 6px; background: linear-gradient(160deg, #b9d3e8 0%, #8fa7b8 45%, #3a3f44 100%); }
  .welcome-lead { position: absolute; left: 281px; top: 733px; width: 370px; font-size: 14px; line-height: 23px; color: var(--ink-dark); }
  .welcome-body { position: absolute; left: 281px; top: 786px; width: 370px; font-size: 11.5px; line-height: 20.5px; color: var(--ink-soft); }

  .news-list { position: absolute; left: 699px; top: 734px; width: 260px; list-style: none; }
  .news-item { position: relative; height: 68px; }
  .news-thumb { position: absolute; left: 0; top: 0; width: 59px; height: 50px; border: 2px solid #fff; box-shadow: 0 0 0 1px #d5d5d5; }
  .news-date { position: absolute; left: 72px; top: 0; font-size: 11.5px; font-weight: 700; color: var(--ink-dark); }
  .news-text { position: absolute; left: 72px; top: 17px; width: 184px; font-size: 11.2px; line-height: 18.5px; color: var(--ink); }

  .footer-rule { position: absolute; left: 75px; width: 880px; height: 1px; background: var(--rule); }
  .footer-col { position: absolute; top: 986px; }
  .footer-col h3 { font-size: 14.5px; font-weight: 400; color: var(--ink-dark); letter-spacing: .2px; }
  .footer-col ul { list-style: none; margin-top: 16px; }
  .footer-col li { font-size: 11.2px; color: var(--ink); height: 24.6px; padding-left: 16px; position: relative; text-transform: uppercase; }
  .footer-col li::before { content: ""; position: absolute; left: 0; top: 4px; width: 5px; height: 5px; border-radius: 50%; background: #999; }
  .partner { position: absolute; }

  .copyright { position: absolute; left: 75px; top: 1151px; font-size: 11.5px; color: var(--ink); }
  .social { position: absolute; top: 1146px; display: flex; gap: 11px; left: 797px; }
  .social span { width: 31px; height: 32px; display: block; }
</style>
</head>
<body>

<header class="site-header">
  <div class="brand">
    <span class="brand-dot"></span>
    <span class="brand-name">Kelva Staffing</span>
  </div>
  <div class="account-links">REGISTER | LOGIN</div>
  <div class="search">Search..
    <svg width="12" height="12" viewBox="0 0 12 12"><circle cx="5" cy="5" r="3.8" fill="none" stroke="#888" stroke-width="1.6"/><line x1="7.8" y1="7.8" x2="11" y2="11" stroke="#888" stroke-width="1.8"/></svg>
  </div>
</header>

<nav class="main-nav">
  <ul>
    <li>Home</li><li>Who We Are</li><li>Our Approach</li><li>What We Do</li><li>Migration Assistance</li><li>Job Seeker</li><li>Useful Links</li><li>Support</li><li>Contact</li>
  </ul>
</nav>

<section class="hero">
  <div class="hero-photo" role="img" aria-label="Team of four smiling business professionals in suits standing in a bright office"></div>
  <div class="hero-copy">
    <h1 class="hero-title">CUSTOM TAILORED BENEFITS</h1>
    <p class="hero-subtitle">DIGNISSIM PHARETRA ERO</p>
    <p class="hero-text">Jerta baditaut onsequser untur magni dolores eoquie volup tate msequi nesciunt. Voluptatem accusantium dolorem.</p>
    <span class="hero-button">REGISTER</span>
  </div>
  <div class="hero-dots"><span class="is-active"></span><span></span><span></span><span></span></div>
</section>

<section class="features">
  <div class="feature" style="left:75px;">
    <svg width="49" height="52" viewBox="0 0 49 52"><polygon points="24.5,0 49,11 24.5,22 0,11" fill="var(--brand-red)"/><polygon points="0,14 22.5,24 22.5,52 0,41" fill="var(--brand-red)"/><polygon points="26.5,24 49,14 49,41 26.5,52" fill="var(--brand-red)"/></svg>
    <div class="feature-title" style="left:67px;">Who We Are</div>
    <div class="feature-sub" style="left:67px;">Lorem Ipsum dolore</div>
    <p class="feature-text">Scing elit vivamus faucibus, mi quis convallisto te mpus, magna elit tincidunt arcu, ac rutrumop tell us nisl sed nisi. Morbi tempor quam vel massa.</p>
  </div>
  <div class="feature" style="left:386px;">
    <svg width="54" height="54" viewBox="0 0 54 54"><g fill="var(--brand-red)"><rect x="22" y="0" width="10" height="54"/><rect x="0" y="22" width="54" height="10"/><rect x="22" y="0" width="10" height="54" transform="rotate(45 27 27)"/><rect x="22" y="0" width="10" height="54" transform="rotate(-45 27 27)"/><circle cx="27" cy="27" r="19"/></g><circle cx="27" cy="27" r="8" fill="#fff"/></svg>
    <div class="feature-title" style="left:67px;">What We Do</div>
    <div class="feature-sub" style="left:67px;">Lorem Ipsum dolore</div>
    <p class="feature-text">Scing elit vivamus faucibus, mi quis convallisto te mpus, magna elit tincidunt arcu, ac rutrumop tell us nisl sed nisi. Morbi tempor quam vel massa.</p>
  </div>
  <div class="feature" style="left:702px;">
    <svg width="62" height="52" viewBox="0 0 62 52"><g fill="var(--brand-red)"><circle cx="40" cy="13" r="11"/><path d="M22 52 C22 34 30 27 40 27 C50 27 62 34 62 52 Z"/><circle cx="20" cy="17" r="11"/><path d="M0 52 C0 38 8 31 20 31 C32 31 38 38 38 52 Z" stroke="#fff" stroke-width="2"/></g></svg>
    <div class="feature-title" style="left:67px;">Job Seekers</div>
    <div class="feature-sub" style="left:67px;">Lorem Ipsum dolore</div>
    <p class="feature-text">Scing elit vivamus faucibus, mi quis convallisto te mpus, magna elit tincidunt arcu, ac rutrumop tell us nisl sed nisi. Morbi tempor quam vel massa.</p>
  </div>
</section>

<section class="welcome">
  <h2 class="section-title" style="left:74px; top:697px;">Welcome to our website</h2>
  <div class="welcome-photo" role="img" aria-label="Two engineers in hard hats on a construction site, one pointing, holding rolled plans"></div>
  <p class="welcome-lead">Ut wisi enim ad minim veniam, quis nostrud exerci tation ulli amcorper suscipit lobortis nisl ut aliquip exea.</p>
  <p class="welcome-body">Incididunt ut labore et dolore magna aliqua. Ut enim ad minim veniam, quis nostrud exercitation ullamcolaboris nisi ut aliquip ex ea commodo consequat. Duis tefd aute iruredolor inreprehenderit in voluptate velit esse cillum.Dolore magna aliqua. Ut enim ad minim veniam, Quisnostru dexercitation ullamco laboris nisi ut aliquip. Ut enim ad mini m veniam, quis nostrud exercitation ullamco laboris. Claritas est etiam p rocessus dynamicus, qui sequitur mutationem.</p>
</section>

<aside class="latest-news">
  <h2 class="section-title" style="left:700px; top:697px;">Latest News</h2>
  <ul class="news-list">
    <li class="news-item">
      <div class="news-thumb" role="img" aria-label="Portrait photo of a young woman" style="background:linear-gradient(135deg,#7a8a3a,#c9a46a);"></div>
      <div class="news-date">During November 2013</div>
      <p class="news-text">our Principal Petrophysicist, quisstr xercitation ullamco labors.</p>
    </li>
    <li class="news-item">
      <div class="news-thumb" role="img" aria-label="Portrait photo of a young boy" style="background:linear-gradient(135deg,#3d6b3a,#b88c6f);"></div>
      <div class="news-date">During November 2013</div>
      <p class="news-text">At vero eois et accusamus et iustoid gnissimos ducimus qui.</p>
    </li>
    <li class="news-item">
      <div class="news-thumb" role="img" aria-label="Portrait photo of a young person" style="background:linear-gradient(135deg,#e8e8e8,#6a5a50);"></div>
      <div class="news-date">During November 2013</div>
      <p class="news-text">Deleniti atque corrupti quos doeset s molestias excepturi sint.</p>
    </li>
  </ul>
</aside>

<footer class="site-footer">
  <div class="footer-rule" style="top:965px;"></div>
  <div class="footer-col" style="left:77px;"><h3>ABOUT US</h3><ul><li>Company Info</li><li>Services</li><li>Team</li><li>Solutions</li></ul></div>
  <div class="footer-col" style="left:241px;"><h3>ADVISE</h3><ul><li>Advise</li><li>FAQs</li><li>Contact</li><li>News</li></ul></div>
  <div class="footer-col" style="left:379px;"><h3>JOIN IN</h3><ul><li>Signup</li><li>Join</li><li>Promotions</li></ul></div>
  <div class="footer-col" style="left:527px;"><h3>LINKS</h3><ul><li>Company Info</li><li>Services</li><li>Team</li><li>Solutions</li></ul></div>
  <div class="footer-col" style="left:695px;"><h3>WE PROUDLY SUPPORT</h3></div>
  <div class="partner" role="img" aria-label="Partner charity badge" style="left:696px; top:1020px; width:142px; height:56px; background:#eef0f6; border-radius:4px;"></div>
  <div class="partner" role="img" aria-label="Partner organisation badge" style="left:873px; top:1023px; width:50px; height:52px; background:#111;"></div>
  <div class="footer-rule" style="top:1129px;"></div>
  <p class="copyright">© 2013 &nbsp;Copyrights. All Rights Reserved.</p>
  <div class="social">
    <span style="background:var(--social-blue);" aria-label="Social profile"></span>
    <span style="background:var(--social-sky);" aria-label="Social profile"></span>
    <span style="background:var(--social-orange);" aria-label="News feed"></span>
    <span style="background:var(--social-red);" aria-label="Video channel"></span>
  </div>
</footer>

</body>
</html>
```